Rice importer and exporter. We need a new design for a 18 kg plastic bag.

We want to create a new brand of rice. This type of rice is produced in southeast Asia, imported to Portugal and sold to the local market. The target are people 30+ years old of all ethnicity. The name of the brand should be 'Marevo', this is the name we want people to see and get used to it. <br/>Regarding the package itself. We want a simple bag, not with many different colours (3, 4 or 5) with preference to golden yellow. The Front page, should have our brand 'Marevo' and the exact description of the type of rice 'Arroz 100% Jasmin Perfumado' and 'Premium Quality'. In the bag should also be included the nutrition facts, cooking instructions, a trasnparent part where customer can see the quality of the product and the our company info. Finally we would like to see in the front page the five stars and on the back the triple AAA (see examples of attached files). All the remaining should be of your imagination. <br/>Finally, the image 3 is an example of a bag structure that we want to make.

Target Market(s)

People 30+ years old

Font styles to use
Serif
Sans Serif

Colors
ffc214
fec214
fee18a
fbee3f
faef58
fbf289

Requirements
Must have
• 5 Stars on the front page, triple A's on the back and a transparent area for the customers to see the quality of the rice.

```html
<!DOCTYPE html>
<html lang="pt">
<head>
<meta charset="utf-8">
<title>Marevo – 18 kg rice bag</title>
<link rel="stylesheet" href="https://fonts.googleapis.com/css2?family=Nunito:ital,wght@0,700;0,800;0,900;1,800&family=Arimo:wght@400;700&display=swap">
<style>
  :root{
    --gold:#ffc214;
    --gold-deep:#f0a800;
    --gold-light:#fee18a;
    --lemon:#fbee3f;
    --lemon-soft:#fbf289;
    --green:#1f6b2a;
    --orange:#e88700;
    --ink:#2b2b2b;
    --white:#ffffff;
    --backdrop:#f2f2f0;
  }
  *{box-sizing:border-box;margin:0;padding:0}
  html,body{width:1200px;height:1136px;overflow:hidden;background:var(--backdrop)}
  body{font-family:"Arimo",Arial,sans-serif;color:var(--ink)}
  .canvas{position:relative;width:1200px;height:1136px;overflow:hidden}

  .section-title{position:absolute;left:760px;top:48px;font-family:"Nunito",sans-serif;font-weight:700;font-size:52px;color:#5a3412}

  /* ---------- front panel ---------- */
  .panel{position:absolute;background:linear-gradient(180deg,var(--gold) 0%,var(--gold-deep) 100%);box-shadow:0 6px 18px rgba(0,0,0,.12)}
  .front{left:50px;top:150px;width:540px;height:930px}
  .front-frame{position:absolute;inset:22px;border:3px solid var(--lemon-soft);border-radius:16px;
    background:radial-gradient(ellipse at 50% 38%,var(--lemon-soft) 0%,var(--lemon) 30%,var(--gold) 70%,var(--gold-deep) 100%);overflow:hidden}
  .quality-ribbon{position:absolute;left:50%;top:26px;transform:translateX(-50%);width:270px;height:40px;
    background:var(--lemon);border:2px solid var(--gold-deep);border-radius:4px;
    font-family:"Nunito",sans-serif;font-style:italic;font-weight:800;font-size:22px;color:var(--green);
    display:flex;align-items:center;justify-content:center}
  .stars{position:absolute;left:50%;top:88px;transform:translateX(-50%);display:flex;gap:6px}
  .stars svg{width:26px;height:26px}
  .brand-name{position:absolute;left:0;right:0;top:112px;text-align:center;
    font-family:"Nunito",sans-serif;font-weight:900;font-size:100px;line-height:1;color:var(--green)}
  .rice-type{position:absolute;left:40px;right:40px;top:236px;height:40px;background:var(--orange);
    color:var(--white);font-family:"Nunito",sans-serif;font-weight:800;font-size:23px;
    display:flex;align-items:center;justify-content:center;border-radius:3px}
  .ornament{position:absolute;left:50%;top:300px;transform:translateX(-50%);width:230px;height:110px;
    background:radial-gradient(ellipse,rgba(232,135,0,.55),rgba(232,135,0,0) 70%)}
  .plate-photo{position:absolute;left:86px;top:420px;width:320px;height:170px;border-radius:50%/40%;
    background:radial-gradient(ellipse at 50% 45%,#ffffff 0%,#f3f1ea 55%,#d9d3c2 100%)}
  .window-band{position:absolute;left:0;right:0;top:598px;height:40px;background:var(--gold-deep);
    clip-path:polygon(0 0,50% 100%,100% 0,100% 40%,50% 140%,0 40%)}
  .rice-window{position:absolute;left:18px;right:18px;top:624px;bottom:18px;
    clip-path:polygon(0 0,50% 40px,100% 0,100% 100%,0 100%);
    background:linear-gradient(180deg,#f7f5ee 0%,#ecebe3 50%,#dcdad0 100%)}
  .net-weight{position:absolute;right:26px;bottom:26px;width:74px;padding:5px 4px;background:var(--lemon);
    border:2px solid var(--gold-deep);text-align:center;font-size:11px;font-weight:700;color:var(--ink)}
  .net-weight strong{display:block;font-size:22px;font-family:"Nunito",sans-serif;font-weight:900}
  .tear-arrow{position:absolute;left:30px;bottom:26px;width:14px;height:26px}

  /* ---------- back panel ---------- */
  .back{left:640px;top:150px;width:510px;height:930px}
  .back-frame{position:absolute;inset:22px;border:3px solid var(--lemon-soft);border-radius:16px;
    background:radial-gradient(ellipse at 40% 30%,var(--lemon-soft) 0%,var(--lemon) 35%,var(--gold) 75%,var(--gold-deep) 100%)}
  .origin-map{position:absolute;left:16px;top:40px;width:230px;height:300px;border-radius:40% 30% 45% 35%;
    background:radial-gradient(ellipse at 50% 40%,#9fb24a 0%,#c7a21e 60%,rgba(240,168,0,0) 100%)}
  .nutrition{position:absolute;right:14px;top:16px;width:196px;background:var(--white);border:2px solid var(--ink);padding:6px}
  .nutrition h2{font-size:13px;font-weight:700;border-bottom:3px solid var(--ink);padding-bottom:4px;margin-bottom:2px}
  .nutrition table{width:100%;border-collapse:collapse;font-size:11px}
  .nutrition td{border-bottom:1px solid #999;padding:6px 0}
  .nutrition td:last-child{text-align:right;font-weight:700}
  .steps{position:absolute;left:14px;right:14px;top:368px;display:grid;grid-template-columns:1fr 1fr;gap:10px 14px}
  .step{display:flex;gap:6px;align-items:center;background:var(--white);border:1px solid var(--gold-deep);padding:6px;height:78px}
  .step-num{flex:none;width:22px;height:22px;border-radius:50%;background:var(--orange);color:var(--white);
    font-size:12px;font-weight:700;display:flex;align-items:center;justify-content:center}
  .step p{flex:1;font-size:11px;line-height:1.3}
  .step-icon{flex:none;width:54px;height:54px;border-radius:4px;background:linear-gradient(180deg,#e9eef2,#c9d3da)}
  .cook-note{position:absolute;left:240px;right:16px;top:650px;font-size:11px;line-height:1.4;font-weight:700;color:var(--ink)}
  .origin{position:absolute;right:18px;top:760px;font-size:10px;font-weight:700}
  .importer{position:absolute;left:16px;bottom:20px;width:240px;font-size:11px;line-height:1.45}
  .importer strong{font-size:12px}
  .grade{position:absolute;right:16px;bottom:20px;width:96px;height:48px;background:var(--ink);color:var(--lemon);
    font-family:"Nunito",sans-serif;font-weight:900;font-size:30px;display:flex;align-items:center;justify-content:center}
</style>
</head>
<body>
<div class="canvas">
  <h1 class="section-title">Tote Design</h1>

  <section class="panel front" aria-label="Front of bag">
    <div class="front-frame">
      <div class="quality-ribbon">Premium Quality</div>
      <div class="stars" aria-label="Five stars">
        <svg viewBox="0 0 24 24"><polygon points="12,1 15,9 23,9 16.5,14 19,22 12,17 5,22 7.5,14 1,9 9,9" fill="#fff8c4" stroke="#e88700"/></svg>
        <svg viewBox="0 0 24 24"><polygon points="12,1 15,9 23,9 16.5,14 19,22 12,17 5,22 7.5,14 1,9 9,9" fill="#fff8c4" stroke="#e88700"/></svg>
        <svg viewBox="0 0 24 24"><polygon points="12,1 15,9 23,9 16.5,14 19,22 12,17 5,22 7.5,14 1,9 9,9" fill="#fff8c4" stroke="#e88700"/></svg>
        <svg viewBox="0 0 24 24"><polygon points="12,1 15,9 23,9 16.5,14 19,22 12,17 5,22 7.5,14 1,9 9,9" fill="#fff8c4" stroke="#e88700"/></svg>
        <svg viewBox="0 0 24 24"><polygon points="12,1 15,9 23,9 16.5,14 19,22 12,17 5,22 7.5,14 1,9 9,9" fill="#fff8c4" stroke="#e88700"/></svg>
      </div>
      <div class="brand-name">Marevo</div>
      <div class="rice-type">Arroz 100% Jasmin Perfumado</div>
      <div class="ornament" role="img" aria-label="Golden dragon ornament with corner scroll motifs"></div>
      <div class="plate-photo" role="img" aria-label="Plate of cooked jasmine rice with vegetables and basil"></div>
      <div class="window-band"></div>
      <div class="rice-window" role="img" aria-label="Transparent window showing the rice grains"></div>
      <svg class="tear-arrow" viewBox="0 0 14 26"><path d="M7 26V4M2 9l5-7 5 7" fill="none" stroke="#d01818" stroke-width="2"/></svg>
      <div class="net-weight">Peso Líquido<strong>18kg</strong></div>
    </div>
  </section>

  <section class="panel back" aria-label="Back of bag">
    <div class="back-frame">
      <div class="origin-map" role="img" aria-label="Map of the growing region filled with rice terraces"></div>
      <div class="nutrition">
        <h2>NUTRITION FACTS:</h2>
        <table>
          <tr><td>Serving Size</td><td>100 g</td></tr>
          <tr><td>Energy</td><td>356 kcal</td></tr>
          <tr><td>Protein</td><td>7 g</td></tr>
          <tr><td>Total Fat</td><td>0.6 g</td></tr>
          <tr><td>Carbohydrate</td><td>79 g</td></tr>
          <tr><td>Fibre</td><td>1.3 g</td></tr>
          <tr><td>Sodium</td><td>5 mg</td></tr>
          <tr><td>Sugars</td><td>0.1 g</td></tr>
        </table>
      </div>
      <div class="steps">
        <div class="step"><span class="step-num">1</span><p>Rinse rice in cold water twice.</p><div class="step-icon" role="img" aria-label="Rinsing rice in a bowl"></div></div>
        <div class="step"><span class="step-num">4</span><p>Cover and simmer 15 minutes.</p><div class="step-icon" role="img" aria-label="Covered pot simmering"></div></div>
        <div class="step"><span class="step-num">2</span><p>Add 1.5 cups water per cup.</p><div class="step-icon" role="img" aria-label="Measuring water into pot"></div></div>
        <div class="step"><span class="step-num">5</span><p>Rest 5 minutes off the heat.</p><div class="step-icon" role="img" aria-label="Pot resting off the stove"></div></div>
        <div class="step"><span class="step-num">3</span><p>Bring to a boil, then stir.</p><div class="step-icon" role="img" aria-label="Pot boiling on stove"></div></div>
        <div class="step"><span class="step-num">6</span><p>Fluff with a fork and serve.</p><div class="step-icon" role="img" aria-label="Rice served in a bowl"></div></div>
      </div>
      <p class="cook-note">For softer rice, add more water. For firmer rice, use less water. Ingredients: 100% Jasmine rice. Store in a cool and dry place.</p>
      <p class="origin">Product of Portugal</p>
      <div class="importer">
        <strong>Importer por: Tao &amp; Vale Lda</strong><br>
        Rua das Palmeiras, Armazém B4<br>
        2700-118 Amadora, Portugal<br>
        Telefone: 210 555 014<br>
        Email: geral@taovale.pt<br>
        www.taovale.pt
      </div>
      <div class="grade">AAA</div>
    </div>
  </section>
</div>
</body>
</html>
```